Business card design needed

Family General Practitioner/ Family Physician.
Logo is the logo of the Noble Guild of Family Healers Oceania
http://kpltw.varendo.example/ImageShelf/marks/pages/NGFHO%20mark_jpg.htm
Updates

Project Deadline Extended
Reason: Just a bit more time to make changes and the weekend for me to look at things closely and to choose. Thanks, Orin

Thanks for all the submissions. So many of them are really works of art. Not one of them are not good. The ones that I am eliminating are the ones that I think are not suitable for me personally only, and because if I don't, it makes it very difficult to decide as many of you are also sending me slight variations of a card. I have just decided to choose a second place card too. Can't thank you all enough. Good luck, Orin. P.S - Working today till 10 pm as the card says :-), so probably won't be able to give a feedback till late Saturday night or Sunday morning here in Sydney, Australia. 

Project Deadline Extended
Reason: Just added a second place to the budget and realised that Australia is ahead of the rest of the world in the time zone (only :-) - don't want to offend anyone or start a debate!! ) , so Monday deadline will mean it will be a weekend for the rest of the world. Just wanted to give everyone more time to submit their best, especially since I will be picking a second card too. Can't thank everyone enough for the submissions. P.S - Not keen on photos on the card.

Industry/Entity Type

Business

Contact Information for Business Card

Dr. Orin Halvey M.B.B.S., F.N.G.F.H.O
Family General Practitioner
Address, timings, phone and fax number on the back.

Requirements
Must have
• Timings
Mon 7 am - 7 pm
Tues 7 am - 12 pm
Wed 7 am - 10 pm
Thurs 7 am - 12 pm
Fri 7 am - 8 pm
Sat 8 am - 10 pm
Sun - Off

```html
<!DOCTYPE html>
<html lang="en">
<head>
<meta charset="utf-8">
<title>Dr. Orin Halvey – Business Card</title>
<link rel="stylesheet" href="https://fonts.googleapis.com/css2?family=Cinzel:wght@500;600&family=Cabin:wght@400;500&display=swap">
<style>
  :root {
    --bg: #e6e7e8;
    --teal-deep: #0f3b39;
    --teal-mid: #1f5a5c;
    --teal-soft: #5b8a99;
    --mist: #f4f8fa;
    --white: #ffffff;
    --sky: #8fb8dc;
    --blue-text: #5e93cc;
    --brown: #4a362c;
    --streak: rgba(150, 120, 100, 0.28);
  }
  * { box-sizing: border-box; margin: 0; padding: 0; }
  html, body { width: 1200px; height: 1000px; overflow: hidden; }
  body {
    background: var(--bg);
    position: relative;
    font-family: "Cabin", sans-serif;
  }

  .card {
    position: absolute;
    width: 720px;
    height: 440px;
    box-shadow: 0 6px 18px rgba(0,0,0,0.25);
    overflow: hidden;
  }

  /* Front */
  .card-front {
    left: 90px;
    top: 40px;
    background:
      radial-gradient(ellipse 60% 45% at 62% 52%, rgba(8,40,38,0.9) 0%, rgba(8,40,38,0) 70%),
      radial-gradient(ellipse 70% 30% at 55% 48%, rgba(120,170,170,0.25) 0%, rgba(120,170,170,0) 70%),
      linear-gradient(100deg, var(--white) 0%, var(--mist) 12%, var(--teal-soft) 32%, var(--teal-mid) 48%, var(--teal-deep) 75%, #163c44 100%);
  }
  .card-front .swirl {
    position: absolute;
    inset: 0;
  }
  .guild-mark {
    position: absolute;
    left: 80px;
    top: 175px;
    width: 140px;
    display: flex;
    align-items: center;
    gap: 8px;
  }
  .guild-mark .dot {
    flex: none;
    width: 14px;
    height: 14px;
    border-radius: 50%;
    background: var(--teal-mid);
  }
  .guild-mark .guild-name {
    font-size: 13px;
    line-height: 1.25;
    color: var(--teal-mid);
    font-weight: 500;
  }
  .identity {
    position: absolute;
    left: 290px;
    top: 178px;
  }
  .doctor-name {
    font-family: "Cinzel", serif;
    font-weight: 600;
    font-size: 33px;
    color: var(--white);
    letter-spacing: 0.5px;
  }
  .credentials {
    margin-top: 10px;
    font-size: 15px;
    letter-spacing: 1.5px;
    color: var(--white);
  }
  .role {
    margin-top: 4px;
    font-size: 21px;
    color: var(--sky);
  }

  /* Back */
  .card-back {
    left: 390px;
    top: 510px;
    background: var(--white);
    color: var(--brown);
  }
  .hours {
    position: absolute;
    left: 55px;
    top: 60px;
  }
  .hours-title {
    font-size: 31px;
    margin-bottom: 10px;
  }
  .hours-row {
    font-size: 22px;
    line-height: 31px;
    white-space: nowrap;
    padding-right: 40px;
    background: linear-gradient(90deg, rgba(255,255,255,0) 0%, var(--streak) 40%, var(--streak) 70%, rgba(255,255,255,0) 100%);
    background-size: 100% 60%;
    background-position: 0 70%;
    background-repeat: no-repeat;
  }
  .hours-row .day { display: inline-block; width: 36px; }
  .hours-row small { font-size: 12px; letter-spacing: 0.5px; }
  .closed { font-size: 15px; margin-top: 2px; }

  .address {
    position: absolute;
    right: 55px;
    top: 40px;
    text-align: right;
    font-size: 24px;
    line-height: 44px;
    color: var(--blue-text);
  }
  .contact {
    position: absolute;
    left: 55px;
    bottom: 28px;
    display: flex;
    align-items: baseline;
    gap: 18px;
  }
  .tel { font-size: 44px; }
  .fax { font-size: 18px; }
</style>
</head>
<body>

  <section class="card card-front" aria-label="Business card front">
    <svg class="swirl" width="720" height="440" viewBox="0 0 720 440" aria-hidden="true">
      <path d="M120 330 C 260 180, 520 150, 700 260" fill="none" stroke="rgba(200,230,230,0.18)" stroke-width="3"/>
      <path d="M200 380 C 360 300, 560 300, 720 360" fill="none" stroke="rgba(200,230,230,0.12)" stroke-width="2"/>
      <path d="M250 120 C 420 60, 600 110, 720 200" fill="none" stroke="rgba(200,230,230,0.1)" stroke-width="2"/>
    </svg>
    <div class="guild-mark">
      <span class="dot"></span>
      <span class="guild-name">Noble Guild of Family Healers Oceania</span>
    </div>
    <div class="identity">
      <h1 class="doctor-name">Dr. Orin Halvey</h1>
      <p class="credentials">M.B.B.S., F.N.G.F.H.O</p>
      <p class="role">Family General Practitioner</p>
    </div>
  </section>

  <section class="card card-back" aria-label="Business card back">
    <div class="hours">
      <h2 class="hours-title">Working hours</h2>
      <p class="hours-row"><span class="day">M</span>7<small>AM</small>...........7<small>PM</small></p>
      <p class="hours-row"><span class="day">Tu</span>7<small>AM</small>.....12<small>PM</small></p>
      <p class="hours-row"><span class="day">W</span>7<small>AM</small>.....................10<small>PM</small></p>
      <p class="hours-row"><span class="day">Th</span>7<small>AM</small>.....12<small>PM</small></p>
      <p class="hours-row"><span class="day">F</span>7<small>AM</small>..............8<small>PM</small></p>
      <p class="hours-row"><span class="day">Sa</span>8<small>AM</small>....................10<small>PM</small></p>
      <p class="closed">Sunday Off</p>
    </div>
    <address class="address">
      Upper Level,<br>
      Linden Court,<br>
      Harwick Towers<br>
      Shopping Centre,<br>
      Harwick Hill,<br>
      NSW 2199.
    </address>
    <div class="contact">
      <span class="tel">Tel: 02 7741 3900</span>
      <span class="fax">Fax: 027741 3911</span>
    </div>
  </section>

</body>
</html>
```